Kestrel Home Business Card Design

We need a business card for a Building company based in Queensland, Australia. Our colours are orange black and we do base all our homes design names and other aspect of our business on astrology. We want the consumer to perceive the company as professional and to attract investors to our company.We have over 20 years in the building industry.We pride ourselves on our innovation of designs and making the building process for anyone from families to investor a smooth and simple experience.
Business
Amelia Prichard0411752116PO Box 454, Mudgeerbaameliaprichard@zodiachomes.com

```html
<!DOCTYPE html>
<html lang="en">
<head>
<meta charset="utf-8">
<title>Kestrel Homes Business Card</title>
<link rel="stylesheet" href="https://fonts.googleapis.com/css2?family=Open+Sans:wght@400;700&display=swap">
<style>
  :root {
    --orange: #f39320;
    --black: #231f20;
    --white: #ffffff;
    --backdrop: #e4e1dc;
  }
  * { margin: 0; padding: 0; box-sizing: border-box; }
  html, body {
    width: 1200px;
    height: 1200px;
    overflow: hidden;
    background: var(--backdrop);
    font-family: "Open Sans", Arial, sans-serif;
  }
  .canvas {
    position: relative;
    width: 1200px;
    height: 1200px;
  }
  .card {
    position: absolute;
    left: 150px;
    width: 900px;
    height: 514px;
    overflow: hidden;
    box-shadow: 0 6px 18px rgba(0,0,0,0.18);
  }
  /* Front */
  .card-front {
    top: 64px;
    background: var(--white);
  }
  .front-brand {
    position: absolute;
    left: 0; right: 0;
    top: 120px;
    display: flex;
    flex-direction: column;
    align-items: center;
    gap: 36px;
  }
  .brand-dot {
    width: 150px;
    height: 150px;
    border-radius: 50%;
    background: var(--orange);
  }
  .brand-name {
    font-weight: 700;
    color: var(--black);
    letter-spacing: -1px;
  }
  .front-brand .brand-name { font-size: 72px; line-height: 1; }

  /* Back */
  .card-back {
    top: 622px;
    background: var(--orange);
  }
  .back-brand {
    position: absolute;
    left: 38px;
    top: 38px;
    display: flex;
    align-items: center;
    gap: 22px;
  }
  .back-brand .brand-dot {
    width: 170px;
    height: 170px;
    background: var(--black);
  }
  .back-brand .brand-name { font-size: 34px; }
  .holder-name {
    position: absolute;
    right: 48px;
    top: 190px;
    font-size: 30px;
    letter-spacing: 2.5px;
    color: var(--black);
  }
  .contact-list {
    position: absolute;
    right: 40px;
    top: 300px;
    list-style: none;
    text-align: right;
    color: var(--black);
    font-size: 23px;
    letter-spacing: 1.6px;
    line-height: 31px;
  }
  .contact-list li {
    display: flex;
    justify-content: flex-end;
    align-items: center;
    gap: 12px;
  }
  .contact-icon { width: 16px; height: 16px; flex: none; }
  .stripe-white {
    position: absolute;
    left: 0; right: 0;
    top: 400px;
    height: 14px;
    background: var(--white);
  }
  .band-black {
    position: absolute;
    left: 0; right: 0;
    top: 414px;
    bottom: 0;
    background: var(--black);
  }
</style>
</head>
<body>
<main class="canvas">
  <section class="card card-front" aria-label="Card front">
    <div class="front-brand">
      <div class="brand-dot" aria-hidden="true"></div>
      <h1 class="brand-name">Kestrel Homes</h1>
    </div>
  </section>

  <section class="card card-back" aria-label="Card back">
    <div class="back-brand">
      <div class="brand-dot" aria-hidden="true"></div>
      <span class="brand-name">Kestrel Homes</span>
    </div>
    <p class="holder-name">Harriet Colvane</p>
    <ul class="contact-list">
      <li>0487309625
        <svg class="contact-icon" viewBox="0 0 16 16" aria-hidden="true"><path fill="#231f20" d="M3.6 1.2l2.3 2.6-1.3 1.9c.9 2 2.6 3.8 4.7 4.8l1.9-1.3 2.6 2.3-1.2 2.3C7.4 15.3.7 8.6 1.2 2.4z"/></svg>
      </li>
      <li>PO Box 872, Wrenbrook
        <svg class="contact-icon" viewBox="0 0 16 16" aria-hidden="true"><path fill="#231f20" d="M8 .8a5 5 0 0 0-5 5c0 3.6 5 9.4 5 9.4s5-5.8 5-9.4a5 5 0 0 0-5-5zm0 7a2 2 0 1 1 0-4 2 2 0 0 1 0 4z"/></svg>
      </li>
      <li>harrietcolvane@kestrelhomes.example
        <svg class="contact-icon" viewBox="0 0 16 16" aria-hidden="true"><rect x="1.5" y="3.5" width="13" height="9" fill="none" stroke="#231f20" stroke-width="1.5"/><path d="M1.5 3.5L8 9l6.5-5.5" fill="none" stroke="#231f20" stroke-width="1.5"/></svg>
      </li>
    </ul>
    <div class="stripe-white"></div>
    <div class="band-black"></div>
  </section>
</main>
</body>
</html>
```